High Tech Real Estate Startup needs a business card

We are developing an innovative real estate marketing product based around advanced search and virtual reality.

We talk to people, we need business cards.

Target Market(s)

The target market is technology professionals and realtors.

Contact Information for Business Card

The information to be included will include

Name
Title
Phone Number
E-mail Address
www.zelquin.com

It should use simple iconography for each one of those fields.

Font styles to use
Other font styles liked:
• Co, Jubilat, Avenir

Colors

Designer to choose colors to be used in the design.

Requirements
Must have
• Clean aesthetic,
• Good use of negative space.
• It should use our company logo, shown in the attached file. It is able to use the negative of that logo (coloured font and white background) and I have attached other acceptable accent colours in a swatch file.
Should not have
• Should not be too busy
• No extraneous text (slogans, tag lines etc)

```html
<!DOCTYPE html>
<html lang="en">
<head>
<meta charset="utf-8">
<title>Zelquin Business Card</title>
<link rel="stylesheet" href="https://fonts.googleapis.com/css2?family=Nunito+Sans:wght@400;600&display=swap">
<style>
  :root {
    --page-bg: #eceae6;
    --card-bg: #ffffff;
    --brand-teal: #0cb4ba;
    --ink-slate: #475a63;
    --band-text: #ffffff;
  }
  * { margin: 0; padding: 0; box-sizing: border-box; }
  html, body {
    width: 1200px;
    height: 1000px;
    overflow: hidden;
    background: var(--page-bg);
    font-family: "Nunito Sans", "Avenir", sans-serif;
  }
  .canvas { position: relative; width: 1200px; height: 1000px; }
  .card {
    position: absolute;
    background: var(--card-bg);
    box-shadow: 0 2px 6px rgba(0,0,0,0.12);
  }
  .card--front { left: 270px; top: 78px; width: 658px; height: 375px; }
  .card--back { left: 270px; top: 534px; width: 660px; height: 376px; }

  .wordmark {
    color: var(--brand-teal);
    font-weight: 600;
    letter-spacing: 1px;
    line-height: 1;
    white-space: nowrap;
  }
  .card--front .wordmark {
    position: absolute;
    left: 0; right: 0;
    top: 148px;
    text-align: center;
    font-size: 78px;
  }

  .identity {
    position: absolute;
    right: 37px;
    top: 98px;
    text-align: right;
    color: var(--ink-slate);
  }
  .identity__name { font-size: 34px; font-weight: 400; line-height: 40px; }
  .identity__title { font-size: 18px; font-weight: 400; line-height: 24px; margin-top: 2px; }

  .divider {
    position: absolute;
    left: 0; top: 181px;
    width: 660px; height: 38px;
  }
  .divider__url {
    position: absolute;
    right: 37px;
    top: 187px;
    font-size: 19px;
    line-height: 26px;
    color: var(--band-text);
    letter-spacing: 0.3px;
  }

  .contacts {
    position: absolute;
    left: 46px;
    top: 248px;
    list-style: none;
    color: var(--ink-slate);
    font-size: 21px;
  }
  .contacts__item {
    display: flex;
    align-items: center;
    height: 35px;
  }
  .contacts__icon { width: 20px; height: 20px; margin-right: 21px; fill: var(--ink-slate); }

  .card--back .wordmark {
    position: absolute;
    right: 37px;
    top: 257px;
    font-size: 62px;
  }
</style>
</head>
<body>
<main class="canvas">
  <section class="card card--front" aria-label="Card front">
    <div class="wordmark">ZELQUIN</div>
  </section>

  <section class="card card--back" aria-label="Card back">
    <div class="identity">
      <p class="identity__name">Name of Person</p>
      <p class="identity__title">Title of Person</p>
    </div>

    <svg class="divider" viewBox="0 0 660 38" aria-hidden="true">
      <line x1="0" y1="1" x2="318" y2="1" stroke="var(--brand-teal)" stroke-width="1.5"/>
      <path d="M315 0 H660 V37 H338 Q329 37 325 28 L318 9 Q316 3 315 0 Z" fill="var(--brand-teal)"/>
    </svg>
    <p class="divider__url">www.zelquin.com</p>

    <ul class="contacts">
      <li class="contacts__item">
        <svg class="contacts__icon" viewBox="0 0 24 24" aria-hidden="true">
          <path d="M6.6 10.8c1.4 2.8 3.8 5.1 6.6 6.6l2.2-2.2c.3-.3.7-.4 1-.2 1.1.4 2.3.6 3.6.6.6 0 1 .4 1 1V20c0 .6-.4 1-1 1C10.6 21 3 13.4 3 4c0-.6.4-1 1-1h3.5c.6 0 1 .4 1 1 0 1.3.2 2.5.6 3.6.1.3 0 .7-.2 1L6.6 10.8z"/>
        </svg>
        <span>+123 456 7890</span>
      </li>
      <li class="contacts__item">
        <svg class="contacts__icon" viewBox="0 0 24 24" aria-hidden="true">
          <path d="M2 6h20v2l-10 6L2 8z M2 10l10 6 10-6v9H2z"/>
        </svg>
        <span>E-mail Address</span>
      </li>
    </ul>

    <div class="wordmark">ZELQUIN</div>
  </section>
</main>
</body>
</html>
```